regPersonal Trainer Flyer Design

Project Deadline Extended
Reason: I have been very busy with other work and would like to extend the deadline to offer designers the chance to edit and improve designs with my help. Thank you for all the designs that have been sent so far.

```html
<!DOCTYPE html>
<html lang="en">
<head>
<meta charset="utf-8">
<title>Personal Trainer Flyer</title>
<link rel="stylesheet" href="https://fonts.googleapis.com/css2?family=Source+Sans+3:wght@300;400;600;700;800&display=swap">
<style>
  :root {
    --sky: #a9ddf3;
    --sky-light: #cdeefb;
    --navy: #1b2a68;
    --ink: #121212;
    --gold: #f2b705;
    --white: #ffffff;
    --photo-warm: #b98a78;
    --photo-cool: #c9c4c6;
  }
  html, body {
    margin: 0;
    padding: 0;
    overflow: hidden;
    background: var(--white);
  }
  .flyer {
    position: relative;
    width: 1200px;
    height: 851px;
    overflow: hidden;
    background: var(--sky);
    font-family: "Source Sans 3", "Myriad Pro", sans-serif;
  }
  .flyer-art {
    position: absolute;
    inset: 0;
  }
  .badge-text {
    position: absolute;
    left: 15px;
    top: 108px;
    width: 160px;
    text-align: center;
    color: var(--white);
    font-weight: 700;
    line-height: 0.98;
  }
  .badge-text .small { font-size: 31px; display: block; }
  .badge-text .big { font-size: 44px; display: block; font-weight: 800; }
  .headline {
    position: absolute;
    left: 334px;
    top: 440px;
    color: var(--ink);
  }
  .headline-main {
    margin: 0;
    font-size: 101px;
    font-weight: 700;
    line-height: 1;
    letter-spacing: -1px;
  }
  .headline-sub {
    margin: 6px 0 0 4px;
    font-size: 50px;
    font-weight: 700;
    letter-spacing: 14px;
    line-height: 1;
  }
  .headline-tag {
    margin: 8px 0 0 2px;
    font-size: 41px;
    font-weight: 400;
    line-height: 1;
  }
  .pitch-list {
    position: absolute;
    left: 798px;
    top: 478px;
    margin: 0;
    padding: 0;
    list-style: none;
    color: var(--ink);
    font-size: 26px;
    font-weight: 600;
    line-height: 35px;
  }
  .pitch-list li {
    position: relative;
    padding-left: 30px;
  }
  .pitch-list li::before {
    content: "";
    position: absolute;
    left: 2px;
    top: 11px;
    border-left: 10px solid var(--ink);
    border-top: 7px solid transparent;
    border-bottom: 7px solid transparent;
  }
  .trainer {
    position: absolute;
    left: 130px;
    top: 742px;
    width: 384px;
    text-align: center;
    color: var(--white);
  }
  .trainer-role {
    font-size: 27px;
    font-weight: 400;
    letter-spacing: 1.5px;
    line-height: 1;
  }
  .trainer-name {
    margin-top: 8px;
    font-size: 47px;
    font-weight: 700;
    line-height: 1;
  }
  .contact {
    position: absolute;
    left: 662px;
    top: 742px;
    margin: 0;
    padding: 0;
    list-style: none;
    color: var(--white);
    font-size: 35px;
    font-weight: 700;
  }
  .contact li {
    display: flex;
    align-items: center;
    height: 44px;
    margin-bottom: 8px;
  }
  .contact svg {
    width: 36px;
    height: 36px;
    margin-right: 20px;
    flex: none;
  }
</style>
</head>
<body>
<main class="flyer">
  <svg class="flyer-art" width="1200" height="851" viewBox="0 0 1200 851" xmlns="http://www.w3.org/2000/svg">
    <defs>
      <clipPath id="top-photos">
        <path d="M0,0 H1200 V474 C700,420 300,232 0,120 Z"/>
      </clipPath>
      <linearGradient id="boxing-tone" x1="0" y1="0" x2="1" y2="1">
        <stop offset="0" stop-color="#d9c9c6"/>
        <stop offset="0.5" stop-color="#a86f5f"/>
        <stop offset="1" stop-color="#4a3a3a"/>
      </linearGradient>
      <linearGradient id="squat-tone" x1="0" y1="0" x2="1" y2="1">
        <stop offset="0" stop-color="#e4e2df"/>
        <stop offset="0.5" stop-color="#9a8c88"/>
        <stop offset="1" stop-color="#3b3b40"/>
      </linearGradient>
      <linearGradient id="barbell-tone" x1="0" y1="0" x2="1" y2="1">
        <stop offset="0" stop-color="#e6dcd8"/>
        <stop offset="0.55" stop-color="#8a6d66"/>
        <stop offset="1" stop-color="#2f2c30"/>
      </linearGradient>
      <linearGradient id="portrait-tone" x1="0" y1="0" x2="0" y2="1">
        <stop offset="0" stop-color="#c7a590"/>
        <stop offset="0.75" stop-color="#b18a78"/>
        <stop offset="1" stop-color="#a9ddf3"/>
      </linearGradient>
    </defs>

    <rect class="list-panel" x="786" y="470" width="414" height="259" fill="var(--sky-light)"/>

    <g role="img" aria-label="Photo of a trainer spotting a client lifting a barbell">
      <path d="M0,100 H420 C380,380 220,520 0,600 Z" fill="url(#barbell-tone)"/>
    </g>
    <path d="M412,250 C370,420 210,530 0,600" fill="none" stroke="var(--white)" stroke-width="16"/>
    <path d="M414,250 C372,424 212,536 0,608" fill="none" stroke="var(--gold)" stroke-width="10"/>

    <g clip-path="url(#top-photos)">
      <g role="img" aria-label="Photo of a client punching a focus pad">
        <rect x="0" y="0" width="598" height="480" fill="url(#boxing-tone)"/>
      </g>
      <g role="img" aria-label="Photo of a client doing a squat while the trainer coaches">
        <rect x="602" y="0" width="598" height="480" fill="url(#squat-tone)"/>
      </g>
    </g>
    <path d="M0,128 C300,242 700,430 1200,484" fill="none" stroke="var(--gold)" stroke-width="10"/>
    <path d="M0,120 C300,232 700,420 1200,474" fill="none" stroke="var(--white)" stroke-width="12"/>

    <g class="badge" transform="translate(95 178)" fill="var(--navy)">
      <circle r="80" fill="var(--white)"/>
      <rect x="-68" y="-68" width="136" height="136" transform="rotate(0)"/>
      <rect x="-68" y="-68" width="136" height="136" transform="rotate(15)"/>
      <rect x="-68" y="-68" width="136" height="136" transform="rotate(30)"/>
      <rect x="-68" y="-68" width="136" height="136" transform="rotate(45)"/>
      <rect x="-68" y="-68" width="136" height="136" transform="rotate(60)"/>
      <rect x="-68" y="-68" width="136" height="136" transform="rotate(75)"/>
    </g>

    <g role="img" aria-label="Head and shoulders portrait of the personal trainer">
      <rect x="158" y="520" width="148" height="210" rx="4" fill="url(#portrait-tone)"/>
    </g>

    <rect class="footer-band" x="0" y="729" width="1200" height="122" fill="var(--navy)"/>
  </svg>

  <div class="badge-text"><span class="small">One</span><span class="big">FREE</span><span class="small">Session</span></div>

  <div class="headline">
    <h1 class="headline-main">FITNESS</h1>
    <p class="headline-sub">TRAINING</p>
    <p class="headline-tag">can be at your home</p>
  </div>

  <ul class="pitch-list">
    <li>Lacking motivation?</li>
    <li>Not achieving your goals?</li>
    <li>Need help?</li>
    <li>Bored of the gym?</li>
    <li>You're never too old</li>
    <li>I can help improve your<br>health and well-being</li>
  </ul>

  <div class="trainer">
    <div class="trainer-role">Personal Trainer</div>
    <div class="trainer-name">Jamie Corran</div>
  </div>

  <ul class="contact">
    <li>
      <svg viewBox="0 0 36 36" aria-hidden="true">
        <circle cx="18" cy="18" r="18" fill="var(--gold)"/>
        <path d="M13,9 l4,0 l1,5 l-3,2 c1,3 3,5 6,6 l2,-3 l5,1 l0,4 c-9,1 -16,-6 -15,-15 z" fill="none" stroke="var(--white)" stroke-width="2.2" stroke-linejoin="round"/>
      </svg>
      <span>07700900123</span>
    </li>
    <li>
      <svg viewBox="0 0 36 36" aria-hidden="true">
        <circle cx="18" cy="18" r="18" fill="var(--gold)"/>
        <rect x="8" y="11" width="20" height="14" rx="1.5" fill="var(--white)"/>
        <path d="M8,12 L18,20 L28,12" fill="none" stroke="var(--gold)" stroke-width="2"/>
      </svg>
      <span>jamiecorran@mailbox.co.uk</span>
    </li>
  </ul>
</main>
</body>
</html>
```